Website design for Puddle Jump Kidscare

I need a website designed for my daycare business, Puddle Jump Kidscare, now that I have a new logo. My former website was ok but simple and I did not have a logo yet. It also was created by me using a template and was entirely pink. I loved the bright, happy feel of it but worried it might not appeal as much to potential clients who have sons. Therefore, I need a site which will appeal to both genders while still keeping the cheerful color scheme of my new logo, which has pinks, blue, green and cream.
Updates

Reason: Hello! I am still trying to download my new logo and am sorry it is taking me so long. Hopefully I will it posted by the end of today (US Eastern Standard Time). Thank you all very much for your patience!

Hello! I have finally managed to upload my new logo for you to use in designing my website. I'm sorry it took so long and greatly appreciate your time and creative efforts! I look forward to seeing what is submitted based on my logo design and its style/colors.

Many thanks!

Reason: As I've been traveling and posted my logo file late, I am extending my deadline. I am now back and can focus on providing more and better feedback. I appreciate your patience and submissions very much!

Reason: I need more time to provide feedback and make decisions.

Industry/Entity Type

Daycare

Colors
0192cd
33a6d7
86cae7
cadf82
fbf289
add136
e34197

```html
<!DOCTYPE html>
<html lang="en">
<head>
<meta charset="utf-8">
<title>Puddle Jump Kidscare</title>
<link href="https://fonts.googleapis.com/css2?family=Open+Sans:wght@400;600;700&display=swap" rel="stylesheet">
<style>
  :root {
    --pink: #e34197;
    --green: #add136;
    --green-text: #9dc43a;
    --grey-nav: #9a9a9a;
    --white: #ffffff;
    --blue: #33a6d7;
    --sky: #86cae7;
  }
  * { margin: 0; padding: 0; box-sizing: border-box; }
  html, body { width: 977px; height: 1200px; overflow: hidden; }
  body { font-family: "Open Sans", sans-serif; background: var(--white); position: relative; }

  .site-header { position: absolute; top: 0; left: 0; width: 977px; height: 150px; }
  .brand { position: absolute; left: 107px; top: 40px; display: flex; align-items: center; gap: 8px; }
  .brand-dot { width: 18px; height: 18px; border-radius: 50%; background: var(--blue); flex: none; }
  .brand-name { font-size: 21px; font-weight: 600; line-height: 1.05; color: var(--pink); }
  .main-nav { position: absolute; top: 65px; right: 107px; display: flex; gap: 12px; }
  .main-nav a { font-size: 9.6px; color: var(--grey-nav); text-decoration: none; text-transform: uppercase; letter-spacing: .2px; }
  .main-nav a.active { color: var(--pink); }

  .hero { position: absolute; top: 150px; left: 0; width: 977px; height: 368px;
    background: linear-gradient(135deg, #6aa23a 0%, #d9463f 22%, #f3d2bd 45%, #f4c9a8 60%, #e6469b 80%, #7bb441 100%); }
  .hero-arrow { position: absolute; top: 318px; width: 28px; height: 28px; border-radius: 50%; background: rgba(120,120,120,.6); }
  .hero-arrow.prev { left: 107px; }
  .hero-arrow.next { left: 842px; }
  .hero-arrow svg { display: block; }
  .hero-dots { position: absolute; top: 499px; left: 385px; display: flex; gap: 2px; }
  .hero-dots span { width: 68px; height: 2px; background: rgba(255,255,255,.45); }
  .hero-dots span.on { background: var(--white); }

  .welcome { position: absolute; top: 544px; left: 107px; width: 763px; text-align: center; }
  .welcome h1 { font-size: 14.5px; font-weight: 400; color: var(--pink); letter-spacing: .2px; margin-bottom: 10px; }
  .welcome p { font-size: 9.8px; line-height: 15.6px; color: var(--green-text); }
  .welcome p + p { margin-top: 15.6px; }

  .features { position: absolute; top: 686px; left: 0; width: 977px; height: 215px; background: var(--green); }
  .feature { position: absolute; top: 18px; width: 246px; text-align: center; color: var(--white); }
  .feature:nth-child(1) { left: 104px; }
  .feature:nth-child(2) { left: 365px; }
  .feature:nth-child(3) { left: 625px; }
  .feature-art { width: 60px; height: 60px; margin: 0 auto 6px; border-radius: 8px; }
  .feature h2 { font-size: 12px; font-weight: 600; margin-bottom: 10px; }
  .feature p { font-size: 9.6px; font-weight: 600; line-height: 15.6px; }

  .news { position: absolute; top: 934px; left: 107px; width: 763px; text-align: center; }
  .news h2 { font-size: 14.5px; font-weight: 400; color: var(--pink); margin-bottom: 16px; }
  .news p { font-size: 9.8px; line-height: 15.6px; color: var(--green-text); }
  .news-date { display: flex; align-items: center; gap: 10px; margin-top: 5px; font-size: 8.5px; color: var(--green-text); }
  .news-date::before, .news-date::after { content: ""; flex: 1; height: 1px; background: var(--pink); }

  .site-footer { position: absolute; top: 1069px; left: 0; width: 977px; height: 131px; background: var(--pink); }
  .footer-brand { position: absolute; left: 107px; top: 38px; display: flex; align-items: center; gap: 8px; }
  .footer-brand .brand-dot { background: var(--white); }
  .footer-brand .brand-name { color: var(--white); }
  .footer-nav { position: absolute; top: 61px; right: 106px; display: flex; gap: 11px; }
  .footer-nav a { font-size: 9.6px; font-weight: 600; color: var(--white); text-decoration: none; text-transform: uppercase; }
  .copyright { position: absolute; top: 105px; right: 106px; font-size: 8px; color: var(--white); }
</style>
</head>
<body>
  <header class="site-header">
    <div class="brand">
      <span class="brand-dot"></span>
      <span class="brand-name">Puddle Jump<br>Kidscare</span>
    </div>
    <nav class="main-nav">
      <a class="active" href="#">Home</a>
      <a href="#">About Us</a>
      <a href="#">Services</a>
      <a href="#">Hours and Fees</a>
      <a href="#">Policies</a>
      <a href="#">Contact Us</a>
      <a href="#">Photos</a>
      <a href="#">Testimonials</a>
    </nav>
  </header>

  <section class="hero" role="img" aria-label="Photo of smiling children lying in a circle on green grass, waving at the camera"></section>
  <div class="hero-arrow prev"><svg width="28" height="28" viewBox="0 0 28 28"><path d="M16 8l-6 6 6 6" fill="none" stroke="#fff" stroke-width="2.4" stroke-linecap="round" stroke-linejoin="round"/></svg></div>
  <div class="hero-arrow next"><svg width="28" height="28" viewBox="0 0 28 28"><path d="M12 8l6 6-6 6" fill="none" stroke="#fff" stroke-width="2.4" stroke-linecap="round" stroke-linejoin="round"/></svg></div>
  <div class="hero-dots"><span class="on"></span><span></span><span></span></div>

  <section class="welcome">
    <h1>Welcome to Puddle Jump Kidscare, a playspace where children can play, create, and imagine!</h1>
    <p>Welcome to Puddle Jump Kidscare, a licensed Group Family Day Care, located in Riverton's beautiful Northgate district. We are located on a pretty, tree-lined block on Willow Lane, between Cedar and Birch Avenues. We are a few blocks from the Green Line tram and the Harbor Road bus route, and we offer flexible hourly childcare, making it as easy as possible for busy parents on the go to arrange their children's care.</p>
    <p>We invite you to learn more about us and hope you will visit us soon!</p>
  </section>

  <section class="features">
    <div class="feature">
      <div class="feature-art" role="img" aria-label="Illustration of a green chalkboard on an easel" style="background: linear-gradient(#1f7a2e, #d9822b);"></div>
      <h2>Learning</h2>
      <p>We develop age-appropriate activities that intro-<br>duce and strengthen academic and social skills.</p>
    </div>
    <div class="feature">
      <div class="feature-art" role="img" aria-label="Illustration of a painter's palette with brush" style="background: linear-gradient(135deg, #d8b27a, #a8733f);"></div>
      <h2>Creativity</h2>
      <p>We offer children a wide range of creative opportu-<br>nities including art projects, toddler yoga lessons, afternoon tea parties, dress up play, and a large selection of books and games.</p>
    </div>
    <div class="feature">
      <div class="feature-art" role="img" aria-label="Illustration of a hand holding a wrapped gift" style="background: linear-gradient(135deg, #f0d0a8, #86cae7);"></div>
      <h2>Sharing</h2>
      <p>We strive to include enrichment activities that extend your child's understanding of the world and their role in it. During our tea parties, for instance, we teach and emphasize good manners so that your child can learn their benefits as they grow.</p>
    </div>
  </section>

  <section class="news">
    <h2>News</h2>
    <p>We are thrilled to have found a new cheerful space with a private backyard! It's large, sunny, and filled with outdoor play equipment such as a toddler slide, sand/water activity table, and lots of toys! Please stay tuned for updates on our program and services as we say goodbye to Winter and hello to Spring!</p>
    <div class="news-date">March 10, 2014</div>
  </section>

  <footer class="site-footer">
    <div class="footer-brand">
      <span class="brand-dot"></span>
      <span class="brand-name">Puddle Jump<br>Kidscare</span>
    </div>
    <nav class="footer-nav">
      <a href="#">Home</a>
      <a href="#">About Us</a>
      <a href="#">Services</a>
      <a href="#">Hours and Fees</a>
      <a href="#">Policies</a>
      <a href="#">Contact Us</a>
      <a href="#">Photos</a>
      <a href="#">Testimonials</a>
    </nav>
    <div class="copyright">Copyright PuddleJumpKidscare 2014. All Rights Reserved</div>
  </footer>
</body>
</html>
```